Pine Hollow Haven Home Inc. Website Update

We have a couple of broken links such as the "contact us" and would like to add board members and a calendar of events. We are open to a new design.

```html
<!DOCTYPE html>
<html lang="en">
<head>
<meta charset="utf-8">
<title>Pine Hollow Haven Home</title>
<link href="https://fonts.googleapis.com/css2?family=Exo+2:wght@400;500;600;700&family=Open+Sans:wght@400;600&display=swap" rel="stylesheet">
<style>
:root{
  --pink:#e8668b;
  --pink-soft:#f7c9d6;
  --pink-pale:#fbe3ea;
  --ink:#222;
  --black:#0d0d0d;
  --dark:#1c1c1c;
  --white:#fff;
  --grey:#666;
}
*{box-sizing:border-box;margin:0;padding:0}
html,body{width:1200px;height:4928px;overflow:hidden}
body{position:relative;background:var(--white);font-family:"Open Sans",Arial,sans-serif;color:var(--ink)}
.section{position:absolute;left:0;width:1200px;overflow:hidden}
h1,h2,h3,.heading{font-family:"Exo 2",Arial,sans-serif}
.btn{display:inline-block;background:var(--pink);color:var(--white);font-family:"Open Sans",Arial,sans-serif;font-size:20px;padding:14px 30px;border-radius:3px}
.wave{position:absolute;left:0;width:1200px}

/* header + hero */
.hero{top:0;height:720px;background:linear-gradient(120deg,#6b5a55,#3f3836 45%,#7a6a62);}
.hero::after{content:"";position:absolute;inset:0;background:rgba(0,0,0,.35)}
.brand{position:absolute;left:112px;top:0;width:220px;height:190px;background:var(--white);border-radius:0 0 110px 110px;z-index:3;display:flex;flex-direction:column;align-items:center;justify-content:center;gap:10px}
.brand-dot{width:34px;height:34px;border-radius:50%;background:var(--pink)}
.brand-name{font-family:"Exo 2",sans-serif;font-weight:600;color:var(--pink);font-size:18px;text-align:center;line-height:1.2;width:170px}
.nav{position:absolute;left:364px;top:44px;display:flex;gap:24px;z-index:3;font-size:17px;color:var(--white)}
.nav a{color:inherit;text-decoration:none}
.nav .active{color:var(--pink)}
.hero-copy{position:absolute;left:0;top:380px;width:1200px;text-align:center;color:var(--white);z-index:2}
.hero-copy h1{font-size:56px;font-weight:600;margin-bottom:18px}
.hero-copy p{font-size:17px;width:600px;margin:0 auto 32px;line-height:1.5}

/* about */
.about{top:720px;height:700px;background:linear-gradient(180deg,#151515,#242424)}
.about-photo{position:absolute;left:104px;top:184px;width:250px;height:250px;border-radius:50%;border:6px solid var(--white);background:linear-gradient(180deg,#c9d6e0,#8f9a86 60%,#5e6b4c)}
.about-copy{position:absolute;left:504px;top:170px;width:600px;color:var(--white)}
.about-copy h2{font-size:44px;font-weight:600;margin-bottom:36px}
.about-copy p{font-size:16px;line-height:1.6;margin-bottom:56px}

/* services */
.services{top:1400px;height:690px}
.title-pink{color:var(--pink);font-size:48px;font-weight:600;text-align:center}
.services .title-pink{position:absolute;top:82px;width:1200px}
.service{position:absolute;top:212px;width:272px;text-align:center}
.service-photo{height:308px}
.service h3{color:var(--pink);font-size:24px;font-weight:500;margin-top:36px}
.arrow{position:absolute;top:336px;width:44px;height:44px;border-radius:50%;background:var(--black)}

/* mission */
.mission{top:2080px;height:580px;background:var(--black);color:var(--white);text-align:center}
.mission h2{margin-top:90px;font-size:44px;font-weight:600}
.mission p{font-size:17px;width:640px;margin:20px auto 0;line-height:1.5}
.steps{position:absolute;top:250px;left:0;width:1200px;height:260px}
.step{position:absolute;width:190px;text-align:center}
.step svg{display:block;margin:0 auto}
.step span{display:block;font-size:15px;font-weight:600;margin-top:14px;line-height:1.4}

/* board */
.board{top:2640px;height:600px}
.board h2{position:absolute;top:80px;width:1200px;text-align:center;font-size:44px;font-weight:600;color:var(--black)}

/* calendar */
.events{top:3200px;height:540px;background:linear-gradient(180deg,#2a2a2a,#141414)}
.events h2{position:absolute;top:44px;width:1200px;text-align:center;color:var(--white);font-size:44px;font-weight:600}
.events-copy{position:absolute;left:148px;top:184px;width:420px;color:var(--white);font-size:17px;line-height:1.7}
.events-copy .btn{margin-top:36px}
.calendar{position:absolute;left:690px;top:140px;width:374px;background:var(--white);border-radius:4px;padding:14px}
.cal-head{background:var(--pink);color:var(--white);text-align:center;font-size:20px;padding:6px 0;font-family:"Exo 2",sans-serif}
.cal-grid{display:grid;grid-template-columns:repeat(7,1fr);gap:4px;margin-top:8px}
.cal-grid div{height:36px;display:flex;align-items:center;justify-content:center;font-size:15px;background:var(--pink-pale);color:var(--ink)}
.cal-grid .dow{background:var(--pink);color:var(--white);height:24px;font-size:12px}

/* testimonials */
.testimonials{top:3720px;height:720px}
.testimonials .title-pink{position:absolute;top:34px;width:1200px;font-size:44px}
.testimonials .sub{position:absolute;top:96px;width:1200px;text-align:center;color:var(--pink);font-size:40px;font-family:"Exo 2",sans-serif}
.testimonials .lead{position:absolute;top:164px;left:280px;width:640px;text-align:center;font-size:16px;line-height:1.6;color:var(--grey)}
.quote-card{position:absolute;width:272px;height:224px;border:3px solid var(--pink-soft);background:var(--white);text-align:center;padding:60px 26px 0}
.quote-card.middle{padding-top:40px;height:228px}
.quote-mark{position:absolute;top:-26px;left:107px;width:52px;height:52px;background:var(--pink);color:var(--white);font-family:"Exo 2",sans-serif;font-size:46px;line-height:62px}
.quote-card p{font-size:14px;line-height:1.5;color:var(--grey)}
.quote-card .who{color:var(--pink);font-size:15px;margin-top:14px}
.avatar{position:absolute;width:84px;height:84px;border-radius:50%;border:4px solid var(--white);box-shadow:0 0 0 2px var(--pink-soft);background:linear-gradient(160deg,#d9b7a0,#8a6a5a)}

/* footer */
.footer{top:4440px;height:488px;background:var(--black);color:var(--white)}
.foot-brand{position:absolute;left:104px;top:90px;width:260px}
.foot-logo{display:flex;align-items:center;gap:12px;margin-bottom:40px}
.foot-logo .brand-dot{width:30px;height:30px}
.foot-logo span{font-family:"Exo 2",sans-serif;font-weight:600;font-size:20px;color:var(--white)}
.foot-brand p{font-size:15px;line-height:1.6}
.foot-col{position:absolute;top:110px}
.foot-col h3{font-size:24px;font-weight:600;margin-bottom:20px}
.foot-col li{list-style:none;font-size:15px;line-height:1.9;display:flex;gap:12px;align-items:flex-start}
.foot-bottom{position:absolute;left:0;top:412px;width:1200px;border-top:1px solid #333}
.copyright{position:absolute;left:104px;top:448px;font-size:14px}
.socials{position:absolute;left:820px;top:438px;display:flex;gap:26px}
.socials span{width:28px;height:28px;background:var(--white);border-radius:4px}
</style>
</head>
<body>

<header class="section hero">
  <div class="brand"><div class="brand-dot"></div><div class="brand-name">Pine Hollow Haven Home</div></div>
  <nav class="nav">
    <a class="active">Home</a><a>About</a><a>How You Can Help</a><a>Services Offered</a><a>Our Love Of Pets</a><a>Contact Us</a><a>Haven Walk</a>
  </nav>
  <div role="img" aria-label="Photo of girls relaxing in the home's living room" style="position:absolute;inset:0"></div>
  <div class="hero-copy">
    <h1>Welcome to Pine Hollow</h1>
    <p>A safe and caring home where young women learn, grow and build independent lives with the steady support of our community.</p>
    <span class="btn">Donate Now</span>
  </div>
  <svg class="wave" style="bottom:-1px;z-index:2" width="1200" height="30" viewBox="0 0 1200 30"><path d="M0 30 L0 10 Q600 34 1200 10 L1200 30Z" fill="#151515"/></svg>
</header>

<section class="section about">
  <div class="about-photo" role="img" aria-label="Photo of the house exterior among spring trees"></div>
  <div class="about-copy">
    <h2>About Us</h2>
    <p>Pine Hollow Haven Home is home to 31 girls ranging in ages from 12-21. The home has seven bedrooms and four bathrooms with a large spa tub for relaxing. Our kitchen takes on the aroma of a restaurant in the evenings as the girls practice their Independent Living Skills with menu planning and preparation in a supervised setting. When the girls are not cooking or relaxing in their rooms, they may be found in the family room where community meetings are held to problem solve.</p>
    <span class="btn">Read More</span>
  </div>
  <svg class="wave" style="bottom:0" width="1200" height="60" viewBox="0 0 1200 60"><path d="M0 60 L0 30 Q600 60 1200 10 L1200 60Z" fill="#fff"/><path d="M0 30 Q600 60 1200 10" stroke="#e8668b" stroke-width="8" fill="none"/></svg>
</section>

<section class="section services">
  <h2 class="title-pink">Services Offered</h2>
  <span class="arrow" style="left:26px"><svg width="44" height="44"><path d="M26 14 L18 22 L26 30" stroke="#fff" stroke-width="4" fill="none"/></svg></span>
  <div class="service" style="left:112px"><div class="service-photo" role="img" aria-label="Photo of two girls unpacking boxes" style="background:linear-gradient(160deg,#e8d6c3,#b89a80)"></div><h3>Independent Living Housing</h3></div>
  <div class="service" style="left:452px"><div class="service-photo" role="img" aria-label="Photo of a cooking and life skills class" style="background:linear-gradient(160deg,#e9c7c9,#a9868a)"></div><h3>Life Skills Classes</h3></div>
  <div class="service" style="left:792px"><div class="service-photo" role="img" aria-label="Photo of girls at a birthday party" style="background:linear-gradient(160deg,#e3e1e6,#a9a3ad)"></div><h3>Birthday Parties</h3></div>
  <span class="arrow" style="left:1130px"><svg width="44" height="44"><path d="M18 14 L26 22 L18 30" stroke="#fff" stroke-width="4" fill="none"/></svg></span>
</section>

<section class="section mission">
  <h2>We are Pine Hollow Haven Home</h2>
  <p>With the help of our community, we have raised over 1000 girls and counting! Some of the services we offer include:</p>
  <div class="steps">
    <svg style="position:absolute;left:0;top:0" width="1200" height="140">
      <g stroke="#fff" stroke-width="3" fill="none" stroke-dasharray="6 6">
        <path d="M340 70 H400"/><path d="M580 70 H630"/><path d="M810 70 H860"/>
      </g>
      <g fill="#fff"><path d="M400 62 L412 70 L400 78Z"/><path d="M630 62 L642 70 L630 78Z"/><path d="M860 62 L872 70 L860 78Z"/></g>
    </svg>
    <div class="step" style="left:150px;top:0">
      <svg width="140" height="140" viewBox="0 0 140 140"><rect x="24" y="24" width="92" height="92" transform="rotate(45 70 70)" fill="#fff"/><g stroke="#111" stroke-width="3" fill="none"><rect x="42" y="62" width="56" height="18"/><path d="M42 80 V90 M98 80 V90 M42 62 V50 M48 62 V55 H64 V62"/></g></svg>
      <span>Room, Board, And Watchful Oversight</span>
    </div>
    <div class="step" style="left:394px;top:0">
      <svg width="140" height="140" viewBox="0 0 140 140"><rect x="24" y="24" width="92" height="92" transform="rotate(45 70 70)" fill="#fff"/><g stroke="#111" stroke-width="3" fill="none"><path d="M40 86 V62 L70 44 L100 62 V86Z"/><rect x="62" y="68" width="16" height="18"/></g></svg>
      <span>Transitional Living Services</span>
    </div>
    <div class="step" style="left:616px;top:0">
      <svg width="140" height="140" viewBox="0 0 140 140"><rect x="24" y="24" width="92" height="92" transform="rotate(45 70 70)" fill="#fff"/><g stroke="#111" stroke-width="3" fill="none"><path d="M70 50 L76 64 L90 64 L79 73 L83 88 L70 79 L57 88 L61 73 L50 64 L64 64Z"/></g></svg>
      <span>Independent Living Services</span>
    </div>
    <div class="step" style="left:854px;top:0">
      <svg width="140" height="140" viewBox="0 0 140 140"><rect x="24" y="24" width="92" height="92" transform="rotate(45 70 70)" fill="#fff"/><g stroke="#111" stroke-width="3" fill="none"><rect x="46" y="60" width="48" height="30"/><rect x="42" y="50" width="56" height="10"/><path d="M70 50 V90"/></g></svg>
      <span>Foster Gift Shop</span>
    </div>
  </div>
  <svg class="wave" style="bottom:0" width="1200" height="60" viewBox="0 0 1200 60"><path d="M0 60 L0 40 Q500 0 1200 30 L1200 60Z" fill="#fff"/><path d="M0 40 Q500 0 1200 30" stroke="#e8668b" stroke-width="8" fill="none"/></svg>
</section>

<section class="section board">
  <h2>Board Members</h2>
  <svg style="position:absolute;left:0;top:200px" width="1200" height="270" viewBox="0 0 1200 270">
    <g role="img" aria-label="Portrait of board chair Marla">
      <polygon points="290,8 390,8 440,135 390,262 290,262 240,135" fill="#2b2b2b"/>
    </g>
    <g role="img" aria-label="Portrait of a board member">
      <polygon points="550,8 650,8 700,135 650,262 550,262 500,135" fill="#b99583"/>
    </g>
    <g role="img" aria-label="Portrait of a board member">
      <polygon points="810,8 910,8 960,135 910,262 810,262 760,135" fill="#c49a86"/>
    </g>
    <text x="340" y="128" text-anchor="middle" fill="#fff" font-family="Exo 2, sans-serif" font-size="30" font-weight="600">Marla</text>
    <text x="340" y="156" text-anchor="middle" fill="#fff" font-family="Open Sans, sans-serif" font-size="17">Ceo</text>
    <g fill="#fff"><rect x="298" y="172" width="16" height="16" rx="2"/><rect x="322" y="172" width="16" height="16" rx="2"/><rect x="346" y="172" width="16" height="16" rx="2"/><rect x="370" y="172" width="16" height="16" rx="2"/></g>
  </svg>
</section>

<section class="section events" role="img" aria-label="Dimmed photo of a community event hall">
  <h2>Calendar of events</h2>
  <div class="events-copy">
    <p>Join us for walks, dinners and open houses throughout the year. Every event helps our girls grow, learn and feel at home.</p>
    <span class="btn">Book Events</span>
  </div>
  <div class="calendar">
    <div class="cal-head">&#8249;&nbsp; April 2019 &nbsp;&#8250;</div>
    <div class="cal-grid">
      <div class="dow">MO</div><div class="dow">TU</div><div class="dow">WE</div><div class="dow">TH</div><div class="dow">FR</div><div class="dow">SA</div><div class="dow">SU</div>
      <div>1</div><div>2</div><div>3</div><div>4</div><div>5</div><div>6</div><div>7</div>
      <div>8</div><div>9</div><div>10</div><div>11</div><div>12</div><div>13</div><div>14</div>
      <div>15</div><div>16</div><div>17</div><div>18</div><div>19</div><div>20</div><div>21</div>
      <div>22</div><div>23</div><div>24</div><div>25</div><div>26</div><div>27</div><div>28</div>
      <div>29</div><div>30</div>
    </div>
  </div>
  <svg class="wave" style="bottom:0" width="1200" height="50" viewBox="0 0 1200 50"><path d="M0 50 L0 20 Q600 50 1200 20 L1200 50Z" fill="#fff"/><path d="M0 20 Q600 50 1200 20" stroke="#e8668b" stroke-width="6" fill="none"/></svg>
</section>

<section class="section testimonials">
  <h2 class="title-pink">Our Testimonials</h2>
  <div class="sub">What Our Girls Say</div>
  <p class="lead">If you're a former resident of the Haven Home and would like to tell us about your experience, please email us at hello@pinehollowhaven.org or come by and see us! You can also friend us on social media, we love to keep in touch!</p>

  <div class="quote-card" style="left:200px;top:310px"><div class="quote-mark">&ldquo;</div><p>"The Haven Home taught me to appreciate things in life more."</p><div class="who">Jenna</div></div>
  <div class="avatar" role="img" aria-label="Portrait of Jenna" style="left:294px;top:560px"></div>

  <div class="avatar" role="img" aria-label="Portrait of Leah" style="left:558px;top:272px"></div>
  <div class="quote-card middle" style="left:464px;top:372px"><p>"While at the Haven Home I learned that nothing, nothing will ever replace family."</p><div class="who">Leah</div></div>

  <div class="quote-card" style="left:730px;top:310px"><div class="quote-mark">&ldquo;</div><p>"Somebody hand me my plan! The Haven Home is like a second home to me, I still visit."</p><div class="who">Carla</div></div>
  <div class="avatar" role="img" aria-label="Portrait of Carla" style="left:824px;top:560px"></div>
</section>

<footer class="section footer">
  <svg class="wave" style="top:0" width="1200" height="40" viewBox="0 0 1200 40"><path d="M0 0 H1200 V10 Q600 44 0 10Z" fill="#fff"/><path d="M0 10 Q600 44 1200 10" stroke="#e8668b" stroke-width="6" fill="none"/></svg>
  <div class="foot-brand">
    <div class="foot-logo"><div class="brand-dot"></div><span>Pine Hollow Haven Home</span></div>
    <p>When the girls are not cooking or relaxing in their rooms, they may be found in the family room where community meetings are held.</p>
  </div>
  <div class="foot-col" style="left:472px">
    <h3>Contact Us</h3>
    <ul>
      <li><svg width="14" height="18" viewBox="0 0 14 18"><path d="M7 1 C3 1 1 4 1 7 C1 11 7 17 7 17 C7 17 13 11 13 7 C13 4 11 1 7 1Z" fill="#fff"/></svg><span>118 Cedar Bend Rd,<br>Millbrook,<br>GA 30000, USA</span></li>
      <li><svg width="16" height="16" viewBox="0 0 16 16"><path d="M3 1 L6 1 L7 5 L5 6 C6 8 8 10 10 11 L11 9 L15 10 L15 13 C15 14 14 15 13 15 C6 15 1 10 1 3 C1 2 2 1 3 1Z" fill="#fff"/></svg><span>555-014-2290</span></li>
      <li><svg width="16" height="14" viewBox="0 0 16 14"><rect x="1" y="2" width="14" height="10" fill="none" stroke="#fff" stroke-width="2"/><path d="M1 2 L8 8 L15 2" stroke="#fff" stroke-width="2" fill="none"/></svg><span>hello@pinehollowhaven.org</span></li>
    </ul>
  </div>
  <div class="foot-col" style="left:832px">
    <h3>Quick Links</h3>
    <ul><li>Home</li><li>About</li><li>How You Can Help</li><li>Services Offered</li><li>Our Love Of Pets</li><li>Contact Us</li><li>Haven Walk</li></ul>
  </div>
  <div class="foot-bottom"></div>
  <div class="copyright">&copy; Pine Hollow Haven Home Inc. 2019. All Rights Reserved</div>
  <div class="socials"><span></span><span></span><span></span><span></span><span></span></div>
</footer>

</body>
</html>
```